Technical Communications firm needs an article turned into a white paper

We want to redesign a 3-part blog series into a white paper that we can print for a conference. I've consolidated the three posts into the attached Word document.

We are looking for a light, easy to read design. Good use of graphics to support the message. I've added the graphics we used in the original post.

You can view them at
http://www.brightquillpages.com/blog/are-you-satisfied-with-your-dita-solution/

Target Market(s)

Product managers from High-tech, Finance, and Medical industries.

Industry/Entity Type

Information Technology

Colors

Designer to choose colors to be used in the design.

Requirements
Must have
• Must be modern, light, easy to read and slick design. Try to incorporate the graphics provided, but feel free to add more. Must retain the lists and tables.
• Must align with our website/brand.
• Must be easy to read. So not too busy.
• Please move all footnotes to endnotes. You'll need to rework the numbering.
Nice to have
• Awesome coverpage.
Should not have
• Hokey clipart. Not too heavy or hard to read.

```html
<!DOCTYPE html>
<html lang="en">
<head>
<meta charset="utf-8">
<title>Are You Satisfied With Your DITA Solution? — White Paper Cover</title>
<link href="https://fonts.googleapis.com/css2?family=Exo+2:wght@400;700;800&display=swap" rel="stylesheet">
<style>
  :root {
    --backdrop: #e9e6e1;
    --paper: #f4f4f2;
    --navy: #0d3a8c;
    --sky: #1fa3dc;
    --charcoal: #2b2b2c;
    --ink-muted: #6a6a6a;
    --mist-light: #e4e2d6;
    --mist-mid: #b9bbb0;
    --mist-dark: #8f948c;
  }
  * { margin: 0; padding: 0; box-sizing: border-box; }
  html, body { width: 1200px; height: 804px; overflow: hidden; }
  body {
    background: var(--backdrop);
    font-family: "Exo 2", sans-serif;
    position: relative;
  }
  .cover {
    position: absolute;
    left: 330px; top: 20px;
    width: 540px; height: 764px;
    background: var(--paper);
    overflow: hidden;
    box-shadow: 0 6px 18px rgba(0,0,0,0.18);
  }
  .cover-bands { position: absolute; inset: 0; }
  .brand {
    position: absolute; right: 44px; top: 40px;
    display: flex; align-items: center; gap: 8px;
  }
  .brand-dot {
    width: 26px; height: 26px; border-radius: 50%;
    background: var(--navy);
  }
  .brand-name {
    font-weight: 700; font-size: 15px; color: var(--navy);
    text-transform: uppercase; letter-spacing: 0.3px;
  }
  .hero-photo {
    position: absolute; left: 0; top: 122px;
    width: 540px; height: 298px;
    background: linear-gradient(180deg, var(--mist-light) 0%, var(--mist-mid) 45%, var(--mist-dark) 100%);
  }
  .title {
    position: absolute; left: 0; right: 30px; top: 470px;
    text-align: right; padding-right: 40px;
    font-weight: 800; font-size: 25px; line-height: 1.2;
    text-transform: uppercase;
  }
  .title-line1 { color: var(--sky); display: block; }
  .title-line2 { color: var(--navy); display: block; padding-right: 38px; }
  .byline {
    position: absolute; right: 70px; top: 548px;
    text-align: center; color: var(--ink-muted);
  }
  .byline-author { font-size: 11px; }
  .byline-role { font-size: 9px; }
  .footer-band {
    position: absolute; left: 0; right: 0; top: 630px; height: 112px;
    background: var(--charcoal);
    display: flex; align-items: center; justify-content: center;
  }
  .footer-url {
    color: #fff; font-size: 15px; letter-spacing: 0.6px; padding-left: 90px;
  }
  .footer-stripe {
    position: absolute; left: 0; right: 0; top: 742px; height: 12px;
    background: var(--sky);
  }
</style>
</head>
<body>
  <main class="cover">
    <div class="hero-photo" role="img" aria-label="Photo: businessman in a suit standing on a stepladder, looking through binoculars over a misty mountain landscape"></div>

    <svg class="cover-bands" width="540" height="764" viewBox="0 0 540 764" aria-hidden="true">
      <polygon points="318,92 540,92 540,104 306,104" fill="var(--sky)"/>
      <polygon points="0,104 312,104 298,122 0,122" fill="var(--navy)"/>
      <polygon points="262,420 540,420 540,436 250,436" fill="var(--navy)"/>
      <polygon points="0,436 262,436 248,452 0,452" fill="var(--sky)"/>
      <rect x="0" y="452" width="540" height="3" fill="#ffffff" opacity="0.6"/>
    </svg>

    <div class="brand">
      <span class="brand-dot"></span>
      <span class="brand-name">Bright Quill Pages</span>
    </div>

    <h1 class="title">
      <span class="title-line1">Are you satisfied with</span>
      <span class="title-line2">your DITA solution?</span>
    </h1>

    <div class="byline">
      <p class="byline-author">By Dana Whitfield</p>
      <p class="byline-role">President of Bright Quill Authoring Solutions Inc.</p>
    </div>

    <div class="footer-band">
      <span class="footer-url">www.brightquillpages.com</span>
    </div>
    <div class="footer-stripe"></div>
  </main>
</body>
</html>
```